Brightcoat Painting Services Requires a New Responsive Site

Hi Designers,

Our current website is this www.brightcoatpainting.com.au for some idea.
I made it on Adobe Muse, its very basic.
I would like it to be redesigned to look more professional and also responsive. I actually know how to do html5 and css but I think others will do this much better than me.

I do not need content because I am a copywriter and would like to do all SEO and copy myself.

The most improtant things to remember is that the site cannot use a CMS
and the code needs to be understandable so that I can go in and add content later on and do SEO work.

Also the site requires an additional testimonial page. I would imagine a nice gallery would be a great addition too(something that I can add images too through html. Also in it is important for it to contain those brand images on the front page as it increases authority. I will attach them onto the brief.

Those two files of nearbyfind and tradeleafs are local directories where we have reviews so a placement of those on the testimonail page would make great sense. I will to the href myself.

Anyway, good luck!

I look forward to see your designs :D
Updates

I have just been informed that on this site websites are simply designed and not built (developed) if this is the case please stop working on your designs and spending more time on this project. I REQUIRE DEVELOPMENT ALSO AND HAVE ALREADY CONTACTED SUPPORT.

Target Market(s)

The target market is 30-75 high income earners.

Industry/Entity Type

Painting

Number of Pages Required

5+ page

Font styles to use
Serif
Sans Serif

Requirements
Must have
• attractive gallery, and the brand icons uploaded.
• must be responsive
• web carousel (with the different types of work we do). eg domestic, commercial, industrial etc.
Nice to have
• a little interactivity
• corporate a natural design that goes well with our logo
Should not have
• any content. just write jiberish to fill in the spaces.
• I will be doing all copy and SEO myself.
• More than five pages, bascially the four that already exist plus the testimonail one.

```html
<!DOCTYPE html>
<html lang="en">
<head>
<meta charset="utf-8">
<title>Brightcoat Painting Services – Testimonials</title>
<link rel="stylesheet" href="https://fonts.googleapis.com/css2?family=Roboto+Condensed:wght@400;700&family=Roboto+Slab:wght@400;700&display=swap">
<style>
  :root {
    --topbar: #0a6fbd;
    --nav: #5cb9ee;
    --nav-active: #c6ecfb;
    --nav-active-text: #1d6fa5;
    --quote: #67cdf5;
    --heading: #3a6e8f;
    --rule: #cfcfcf;
    --page-side: #ececec;
    --footer: #d9d9db;
    --ink: #111111;
    --white: #ffffff;
    --listing-blue: #1aa9e6;
    --listing-yellow: #f4dc0a;
    --badge: #2d4c8c;
  }
  * { box-sizing: border-box; margin: 0; padding: 0; }
  html, body { width: 678px; height: 1200px; overflow: hidden; }
  body { position: relative; background: var(--page-side); font-family: "Roboto Slab", serif; color: var(--ink); }

  .call-bar { position: absolute; top: 0; left: 0; width: 678px; height: 29px; background: var(--topbar);
    color: var(--white); font: 700 17px/29px "Roboto Condensed", sans-serif; padding-left: 38px; letter-spacing: .3px; }

  .site-header { position: absolute; top: 29px; left: 0; width: 678px; height: 103px; background: #f6f6f6; }
  .brand { position: absolute; top: 0; left: 0; width: 678px; height: 103px; display: flex; align-items: center; justify-content: center; gap: 14px; }
  .brand-mark { width: 34px; height: 34px; background: var(--topbar); }
  .brand-name { font: 700 22px "Roboto Condensed", sans-serif; color: var(--ink); letter-spacing: .6px; }

  .main-nav { position: absolute; top: 132px; left: 0; width: 678px; height: 35px; background: var(--nav); }
  .main-nav a { position: absolute; top: 0; height: 35px; line-height: 35px; font: 400 14px/35px "Roboto Condensed", sans-serif; color: var(--ink); text-decoration: none; }
  .main-nav a.is-current { background: var(--nav-active); color: var(--nav-active-text); text-align: center; }

  .content { position: absolute; top: 167px; left: 31px; width: 619px; height: 790px; background: var(--white); }

  .carousel { position: absolute; top: 22px; left: 6px; width: 606px; height: 240px; border: 1px solid #c8c8c8; overflow: hidden; }
  .carousel-photo { position: absolute; inset: 0; background: linear-gradient(180deg, #5f9ad6 0%, #9cc2e6 45%, #d7d9d8 62%, #a9aaa6 85%, #6f8a4e 100%); }
  .carousel-arrow { position: absolute; top: 103px; width: 30px; height: 30px; }
  .carousel-caption { position: absolute; top: 140px; left: 0; width: 606px; text-align: center; color: var(--white); }
  .carousel-title { font: 700 22px/26px "Roboto Slab", serif; letter-spacing: .4px; }
  .carousel-text { font: 400 12.5px/15px "Roboto Condensed", sans-serif; width: 330px; margin: 2px auto 0; }
  .carousel-dots { position: absolute; top: 217px; left: 0; width: 606px; display: flex; justify-content: center; gap: 11px; }
  .carousel-dots span { width: 5px; height: 5px; border-radius: 50%; background: var(--white); }

  .section-title { position: absolute; top: 293px; left: 11px; font: 400 17px "Roboto Slab", serif; color: var(--heading); text-transform: uppercase; }
  .section-rule { position: absolute; left: 7px; width: 592px; height: 1px; background: var(--rule); }

  .testimonial { position: absolute; left: 8px; width: 577px; }
  .testimonial-quote { position: relative; background: var(--quote); color: var(--white); height: 77px;
    padding: 5px 10px 0 4px; font: 400 10.4px/15px "Roboto Slab", serif; }
  .testimonial-quote::after { content: ""; position: absolute; left: 22px; bottom: -14px; border-left: 13px solid transparent; border-right: 13px solid transparent; border-top: 14px solid var(--quote); }
  .mark { font-size: 15px; font-weight: 700; line-height: 0; vertical-align: -3px; }
  .testimonial-author { margin: 21px 0 0 7px; font: 400 10.6px "Roboto Slab", serif; }

  .site-footer { position: absolute; top: 957px; left: 0; width: 678px; height: 243px; background: var(--footer); }
  .footer-note { position: absolute; top: 12px; width: 678px; text-align: center; font: 400 10.6px "Roboto Slab", serif; }
  .listing { position: absolute; top: 40px; }
  .footer-rule { position: absolute; left: 38px; width: 601px; height: 1px; background: #a8a8aa; }
  .partner { position: absolute; top: 134px; font: 700 13px "Roboto Slab", serif; color: #2a2a2a; text-align: center; width: 110px; }
  .badge { position: absolute; top: 124px; left: 536px; width: 34px; height: 40px; background: var(--badge); border-radius: 4px 4px 17px 17px; }
  .footer-contact { position: absolute; top: 185px; font: 700 10.6px "Roboto Slab", serif; }
  .copyright { position: absolute; top: 223px; left: 67px; font: 400 6.5px "Roboto Condensed", sans-serif; }
</style>
</head>
<body>
  <div class="call-bar">CALL US TODAY: 1300 555 014</div>

  <header class="site-header">
    <div class="brand">
      <span class="brand-mark"></span>
      <span class="brand-name">BRIGHTCOAT PAINTING</span>
    </div>
  </header>

  <nav class="main-nav">
    <a href="#" style="left:49px">Home</a>
    <a href="#" style="left:132px">Services</a>
    <a href="#" style="left:234px">Gallery</a>
    <a href="#" class="is-current" style="left:309px;width:97px">Testimonials</a>
    <a href="#" style="left:451px">Contact Us</a>
  </nav>

  <main class="content">
    <section class="carousel">
      <div class="carousel-photo" role="img" aria-label="Photo of a freshly painted white weatherboard family home under a blue sky"></div>
      <svg class="carousel-arrow" style="left:33px" viewBox="0 0 30 30" aria-hidden="true">
        <circle cx="15" cy="15" r="13.5" fill="none" stroke="#fff" stroke-width="2"/>
        <path d="M18 8 L9 15 L18 22 L15 15 Z" fill="#fff"/>
      </svg>
      <svg class="carousel-arrow" style="left:544px" viewBox="0 0 30 30" aria-hidden="true">
        <circle cx="15" cy="15" r="13.5" fill="none" stroke="#fff" stroke-width="2"/>
        <path d="M12 8 L21 15 L12 22 L15 15 Z" fill="#fff"/>
      </svg>
      <div class="carousel-caption">
        <h2 class="carousel-title">DOMESTIC PAINTING</h2>
        <p class="carousel-text">At Brightcoat painting we are focused on superior quality and workmanship.</p>
      </div>
      <div class="carousel-dots"><span></span><span></span><span></span></div>
    </section>

    <h1 class="section-title">Testimonials</h1>
    <div class="section-rule" style="top:317px"></div>

    <article class="testimonial" style="top:322px">
      <blockquote class="testimonial-quote"><span class="mark">“</span>Lorem ipsum dolor sit amet, consectetuer adipiscing elit. Aenean commodo ligula eget dolor. Aenean massa.<br>Cum sociis natoque penatibus et magnis dis parturient montes, nascetur ridiculus mus. Donec quam felis, ultricies nec, pellentesque eu, pretium quis, sem. Nulla consequat massa quis enim. Donec pede justo, fringilla vel, aliquet nec, vulputate eget, arcu. <span class="mark">”</span></blockquote>
      <p class="testimonial-author">Sam Carter - Web Master</p>
    </article>
    <div class="section-rule" style="top:458px"></div>

    <article class="testimonial" style="top:464px">
      <blockquote class="testimonial-quote"><span class="mark">“</span>Lorem ipsum dolor sit amet, consectetuer adipiscing elit. Aenean commodo ligula eget dolor. Aenean massa.<br>Cum sociis natoque penatibus et magnis dis parturient montes, nascetur ridiculus mus. Donec quam felis, ultricies nec, pellentesque eu, pretium quis, sem. Nulla consequat massa quis enim. Donec pede justo, fringilla vel, aliquet nec, vulputate eget, arcu. <span class="mark">”</span></blockquote>
      <p class="testimonial-author">Sam Carter - Web Master</p>
    </article>
    <div class="section-rule" style="top:607px"></div>

    <article class="testimonial" style="top:613px">
      <blockquote class="testimonial-quote"><span class="mark">“</span>Lorem ipsum dolor sit amet, consectetuer adipiscing elit. Aenean commodo ligula eget dolor. Aenean massa.<br>Cum sociis natoque penatibus et magnis dis parturient montes, nascetur ridiculus mus. Donec quam felis, ultricies nec, pellentesque eu, pretium quis, sem. Nulla consequat massa quis enim. Donec pede justo, fringilla vel, aliquet nec, vulputate eget, arcu. <span class="mark">”</span></blockquote>
      <p class="testimonial-author">Sam Carter - Web Master</p>
    </article>
  </main>

  <footer class="site-footer">
    <p class="footer-note">To see more of our testimonials visit nearbyfind and tradeleafs, by clicking on the icons below.</p>
    <a href="#" class="listing" style="left:240px" aria-label="nearbyfind reviews">
      <svg width="60" height="59" aria-hidden="true"><rect width="60" height="59" fill="var(--listing-blue)"/></svg>
    </a>
    <a href="#" class="listing" style="left:378px" aria-label="tradeleafs reviews">
      <svg width="56" height="59" aria-hidden="true"><rect width="56" height="59" rx="5" fill="var(--listing-yellow)"/></svg>
    </a>
    <div class="footer-rule" style="top:107px"></div>

    <span class="partner" style="left:63px">Rivuko</span>
    <span class="partner" style="left:217px">Hollend</span>
    <span class="partner" style="left:355px">Tarrowin</span>
    <span class="badge" aria-label="Workmanship warranty badge"></span>

    <p class="footer-contact" style="left:68px">Address:&nbsp; Larkvale Victoria 3999, Australia</p>
    <p class="footer-contact" style="left:380px">Email:&nbsp; info@brightcoatpainting.com.au</p>
    <div class="footer-rule" style="top:213px"></div>
    <p class="copyright">© 2014 Brightcoat Painting. All rights reserved.</p>
  </footer>
</body>
</html>
```